Business Card Design Project (on hold until logo completed)

Small Pharma Consulting Firm called "Shorebeam" Pharma Solutions. Small business will be focused on ad hoc consulting projects. Business located near the beach so want to play off the location with the "ideas" so a "house of lights or ideas". The concept is to use a variety of experiences and expertise in the Pharma business to help clients use what they already know to tell a story and create ideas that better build customer solutions. Simplicity is key. We hire lots of consultants, create lots of data, conduct lots of research but we often get lost in all of it or do not have time to digest and analyze. We also get inwardly-focused. This small group will compress the information into simple chunks from a customer persective through a unique blend of skills and tools.
Updates

Project Deadline Extended
Reason: Logo is now completed so can begin business card design

Target Market(s)

Pharma Professionals, mostly marketing and analytics but could also be senior leadership

Industry/Entity Type

Business

Font styles to use
Sans Serif

Colors
00a990
fcca95
faa54b

Requirements
Must have
• logo with text
Nice to have
• Space for PO Box on 1 line, then city, state, zip on next line
Background should be white or tan/beige (to be eco-friendly, like the color of a brown paper bag)

```html
<!DOCTYPE html>
<html lang="en">
<head>
<meta charset="utf-8">
<title>Shorebeam Pharma Solutions – Business Card</title>
<link href="https://fonts.googleapis.com/css2?family=Lato:wght@400;700;900&display=swap" rel="stylesheet">
<style>
  :root {
    --teal: #00a990;
    --peach: #fcca95;
    --orange: #faa54b;
    --kraft-light: #e3d7bb;
    --kraft: #cfbf99;
    --ink: #3a3328;
    --stage: #efeae0;
  }
  * { box-sizing: border-box; margin: 0; padding: 0; }
  html, body {
    width: 1200px; height: 600px; overflow: hidden;
    background: var(--stage);
    font-family: "Lato", Arial, sans-serif;
  }
  .business-card {
    position: absolute; left: 180px; top: 60px;
    width: 840px; height: 480px;
    border-radius: 22px; overflow: hidden;
    background: linear-gradient(135deg, var(--kraft-light) 0%, var(--kraft) 100%);
    box-shadow: 0 10px 30px rgba(0,0,0,.18);
  }
  .brand {
    position: absolute; left: 64px; top: 176px;
    display: flex; align-items: center; gap: 16px;
  }
  .brand-mark {
    width: 50px; height: 50px; border-radius: 50%;
    background: var(--orange);
  }
  .brand-name {
    font-weight: 900; font-size: 44px; letter-spacing: 1px;
    color: var(--teal); text-transform: uppercase; line-height: 1;
  }
  .brand-tagline {
    font-weight: 900; font-size: 15px; letter-spacing: 4px; text-transform: uppercase;
    color: var(--teal); margin-top: 6px;
  }
  .divider {
    position: absolute; left: 64px; right: 64px; top: 296px;
    height: 2px; background: var(--peach);
  }
  .divider-short {
    position: absolute; right: 64px; top: 128px;
    width: 180px; height: 2px; background: var(--peach);
  }
  .contact-list {
    position: absolute; left: 64px; top: 330px;
    list-style: none; font-size: 17px; color: var(--ink);
  }
  .contact-list li { display: flex; align-items: center; gap: 12px; margin-bottom: 10px; }
  .contact-list svg { width: 18px; height: 18px; flex: none; }
  .person {
    position: absolute; right: 64px; top: 58px; text-align: right;
  }
  .person-name {
    font-variant: small-caps; font-weight: 700; font-size: 30px;
    color: var(--teal); letter-spacing: 1px; line-height: 1;
  }
  .person-role {
    font-variant: small-caps; font-size: 19px; color: var(--ink);
    letter-spacing: 1px; margin-top: 4px;
  }
  .address {
    position: absolute; right: 64px; top: 170px; text-align: right;
    font-size: 17px; line-height: 1.45; color: var(--ink);
  }
  .edge-band {
    position: absolute; left: 0; right: 0; bottom: 0; height: 26px;
    display: flex;
  }
  .edge-band .band-teal { width: 22%; background: var(--teal); }
  .edge-band .band-plain { flex: 1; }
  .edge-band .band-peach { width: 8%; background: var(--peach); }
  .edge-band .band-orange { width: 20%; background: var(--orange); }
</style>
</head>
<body>
  <div class="business-card">
    <div class="person">
      <div class="person-name">Daniel Ferro</div>
      <div class="person-role">Manager</div>
    </div>
    <div class="divider-short"></div>
    <div class="address">Your Home or Business<br>Address Here</div>

    <div class="brand">
      <div class="brand-mark"></div>
      <div>
        <div class="brand-name">Shorebeam</div>
        <div class="brand-tagline">Pharma Solutions</div>
      </div>
    </div>

    <div class="divider"></div>

    <ul class="contact-list">
      <li>
        <svg viewBox="0 0 18 18"><rect x="1" y="1" width="16" height="16" rx="2" fill="var(--teal)"/><path d="M6 4.5c-.8.4-1.4 1.2-1 2.6.7 2.6 3.3 5.2 5.9 5.9 1.4.4 2.2-.2 2.6-1l-1.8-1.4-1.1.8c-1.2-.5-2.5-1.8-3-3l.8-1.1z" fill="#fff"/></svg>
        0400 215 738
      </li>
      <li>
        <svg viewBox="0 0 18 18"><rect x="1" y="1" width="16" height="16" rx="2" fill="var(--teal)"/><path d="M4.5 9.5l3 3 6-6.5" stroke="#fff" stroke-width="2" fill="none"/></svg>
        hello@shorebeampharma.com
      </li>
      <li>
        <svg viewBox="0 0 18 18"><rect x="1.5" y="1.5" width="15" height="15" rx="2" fill="none" stroke="var(--ink)" stroke-width="1.5"/></svg>
        www.shorebeampharma.com
      </li>
    </ul>

    <div class="edge-band">
      <div class="band-teal"></div>
      <div class="band-plain"></div>
      <div class="band-peach"></div>
      <div class="band-orange"></div>
    </div>
  </div>
</body>
</html>
```